Corporate Business Card

Very professional, Modern, Not to busy, include phone address email, website
(253) 617-4930, 18761 52nd Avenue S, Kent, WA 98047, martin@plumlinegroup.com, varkoworks.com

Target Market(s)

Manufacturing

Industry/Entity Type

Aero, machining, manufacturing, Off road racing

Contact Information for Business Card

Phone, address email, website

```html
<!DOCTYPE html>
<html lang="en">
<head>
<meta charset="utf-8">
<title>Varko Works – Business Card</title>
<link href="https://fonts.googleapis.com/css2?family=Open+Sans:wght@400;600;700&display=swap" rel="stylesheet">
<style>
  :root {
    --navy: #1b3570;
    --navy-back: #22376d;
    --navy-deep: #152a5c;
    --red: #d42a2f;
    --white: #ffffff;
    --backdrop: #8b8b89;
  }
  * { margin: 0; padding: 0; box-sizing: border-box; }
  html, body { width: 1200px; height: 801px; overflow: hidden; }
  body {
    background: var(--backdrop);
    font-family: "Open Sans", Arial, sans-serif;
    position: relative;
  }
  .card {
    position: absolute;
    top: 252px;
    width: 520px;
    height: 297px;
    border-radius: 16px;
    overflow: hidden;
    border: 1.5px solid var(--red);
  }
  .card-front { left: 50px; background: var(--white); }
  .card-back { left: 630px; background: var(--navy-back); }
  .card-art { position: absolute; inset: 0; }
  .brand-name {
    position: absolute;
    font-family: "Open Sans", Arial, sans-serif;
    font-weight: 700;
    white-space: nowrap;
  }
  .card-front .brand-name {
    left: 38px; top: 62px;
    font-size: 38px;
    color: var(--navy);
    letter-spacing: 1px;
  }
  .card-back .brand-name {
    left: 0; right: 0; top: 118px;
    text-align: center;
    font-size: 50px;
    color: var(--navy-deep);
    letter-spacing: 2px;
  }
  .address {
    position: absolute;
    right: 222px; top: 196px;
    text-align: right;
    color: var(--white);
    font-size: 13.5px;
    line-height: 20px;
  }
  .address .company { color: var(--red); font-weight: 600; }
  .divider {
    position: absolute;
    left: 312px; top: 178px;
    width: 1.5px; height: 78px;
    background: var(--red);
  }
  .contact-list {
    position: absolute;
    left: 326px; top: 176px;
    list-style: none;
    color: var(--white);
    font-size: 13px;
    line-height: 26px;
  }
  .contact-list li { display: flex; align-items: center; gap: 7px; white-space: nowrap; }
  .contact-list svg { width: 12px; height: 12px; flex: none; }
</style>
</head>
<body>
  <section class="card card-front">
    <svg class="card-art" viewBox="0 0 520 297" preserveAspectRatio="none" aria-hidden="true">
      <path d="M0 232 Q330 196 402 0 L520 0 L520 297 L0 297 Z" fill="var(--navy)"/>
      <path d="M0 220 Q318 186 388 0" fill="none" stroke="var(--red)" stroke-width="3"/>
    </svg>
    <div class="brand-name">Varko Works</div>
    <div class="address">
      <div class="company">Varko Works</div>
      <div>18761 52nd Avenue S</div>
      <div>Kent, WA 98047</div>
    </div>
    <div class="divider"></div>
    <ul class="contact-list">
      <li>
        <svg viewBox="0 0 12 12"><circle cx="6" cy="6" r="6" fill="var(--red)"/><path d="M4 3.2l1 .1.5 1.4-.7.6a4 4 0 0 0 1.9 1.9l.6-.7 1.4.5.1 1c-.3.5-.8.7-1.4.6A5 5 0 0 1 3.4 4.6c-.1-.6.1-1.1.6-1.4z" fill="var(--white)"/></svg>
        (253) 617-4930
      </li>
      <li>
        <svg viewBox="0 0 12 12"><rect x="0.5" y="2" width="11" height="8" rx="1" fill="var(--red)"/><path d="M1 2.6l5 3.6 5-3.6" fill="none" stroke="var(--white)" stroke-width="1"/></svg>
        martin@plumlinegroup.com
      </li>
      <li>
        <svg viewBox="0 0 12 12"><circle cx="6" cy="6" r="5.3" fill="var(--red)"/><g fill="none" stroke="var(--white)" stroke-width=".8"><circle cx="6" cy="6" r="3.8"/><ellipse cx="6" cy="6" rx="1.6" ry="3.8"/><path d="M2.2 6h7.6"/></g></svg>
        varkoworks.com
      </li>
    </ul>
  </section>

  <section class="card card-back">
    <div class="brand-name">Varko Works</div>
  </section>
</body>
</html>
```